Personal Trainer website design

We are working with a personal trainer to design a website. They offer their primary services: Diet Coaching, In-Person Coaching (workouts), and Remote Coaching.
Some sites we like: https://www.mirabelthorne.com, https://kavialune.com/en-us, https://corvexfit.co.uk
Thank you for taking the time to consider designing a website for us. We are web developers based in Stockton, CA USA. Most of our projects go through the same process. Understanding this process may help you win a project with us. We custom-code all of our websites in-house. We don’t have any requirements as to what tools you use for your design, but ask that you follow these guidelines.
IMAGES:
We ask that if you use any images, or icons in the design, have a link to the asset, so we can purchase the image/icon. Most of the designs we submit do not have the customer’s images on them unless they have some great images. Be creative; show us the feeling that you are trying to portray with your image choices. Use any royalty-free site you choose. We subscribe to Quillon and mostly use their images, but are ok to purchase images outside of Quillon.
FONTS:
We ask that you identify the fonts you’re using in the design. This can be done in a message if you want. We typically use Brivane Fonts and Quillon Fonts.
CONTENT:
We're always open to different content and ideas. Often, we submit designs with stock images so that the client can see our vision. We typically go back and take pictures after the website launch to use their images with our vision. Lorem Ipsum is fine for paragraphs, but we ask that you make the Headers with correct English. We want to be able to show the vision and identify the sections of the website.
INSPIRATION:
We try and add a couple of links in the brief of some websites that we like to help you get started in your design.
REVISIONS:
We do not often ask for revisions of the designs unless we see something in the design that may not appeal to the client. If there are slight changes that we want to make, we simply do that in the development process.
FEEDBACK:
We rarely give feedback on designs during the design process. We are working on many website projects and do not have the time to give feedback. We usually respond if your request is well thought out and asks specific questions, but a note asking “feedback, please” usually goes unanswered.
1 page

```html
<!DOCTYPE html>
<html lang="en">
<head>
<meta charset="utf-8">
<title>Veltrafit — Personal Training</title>
<link rel="stylesheet" href="https://fonts.googleapis.com/css2?family=Poppins:wght@400;500;600;700;800&family=Inter:wght@400;500&display=swap">
<style>
:root{
  --olive:#7f8a1b;
  --olive-bright:#8e9a1c;
  --olive-deep:#6f7815;
  --ink:#111111;
  --sand:#d9d4cf;
  --ring:#dcd6d0;
  --white:#ffffff;
  --text:#222222;
}
*{margin:0;padding:0;box-sizing:border-box}
html,body{width:1200px;height:2925px;overflow:hidden;background:var(--white)}
body{position:relative;font-family:'Inter',sans-serif;color:var(--text)}
.abs{position:absolute}
.btn{position:absolute;display:flex;align-items:center;justify-content:center;background:var(--olive-bright);color:var(--white);font-family:'Poppins',sans-serif;font-weight:700;font-size:18px;border-radius:26px;box-shadow:3px 4px 6px rgba(0,0,0,.25)}
.site-header{position:absolute;left:0;top:0;width:1200px;height:91px;background:var(--white)}
.brand{position:absolute;display:flex;align-items:center;gap:10px;font-family:'Poppins',sans-serif;font-weight:700;color:var(--ink)}
.brand-dot{border-radius:50%;background:var(--olive)}
.main-nav a{position:absolute;top:30px;font-family:'Poppins',sans-serif;font-size:16px;color:#333;text-decoration:none}
.main-nav .active{color:var(--olive-bright);font-weight:600;font-size:18px;top:28px;border-bottom:2px solid var(--olive-bright);padding-bottom:1px}
.hero{position:absolute;left:0;top:91px;width:1200px;height:660px;background:linear-gradient(100deg,#4a3a26 0%,#6b5235 30%,#1e3550 60%,#0f2b47 100%)}
.hero-title{position:absolute;left:97px;top:126px;font-family:'Poppins',sans-serif;font-weight:700;font-size:52px;line-height:69px;color:var(--white)}
.hero-text{position:absolute;left:97px;top:260px;width:380px;font-size:15px;line-height:31px;color:var(--white)}
.dot{position:absolute;width:15px;height:15px;border-radius:50%;background:#9a9a9a}
.section-title{position:absolute;font-family:'Poppins',sans-serif;font-weight:600;font-size:32px}
.about-text{position:absolute;left:95px;top:858px;width:510px;font-size:15px;line-height:31px;color:var(--text)}
.service-photo{position:absolute;width:318px;height:330px;border-radius:50%;border:6px solid var(--ring)}
.service-name{position:absolute;width:340px;text-align:center;font-family:'Poppins',sans-serif;font-weight:600;font-size:28px;color:var(--white)}
.field{position:absolute;border:2px solid var(--ink);font-size:15px;padding:14px 15px;color:#333}
.site-footer{position:absolute;left:0;top:2418px;width:1200px;height:507px;background:var(--sand)}
.footer-nav a{position:absolute;top:280px;font-family:'Poppins',sans-serif;font-size:16px;color:#222;text-decoration:none}
.contact-icon{position:absolute;width:49px;height:49px;background:#1e1e1e;display:flex;align-items:center;justify-content:center}
.contact-text{position:absolute;font-size:17px;color:var(--ink)}
</style>
</head>
<body>

<header class="site-header">
  <div class="brand" style="left:97px;top:24px;font-size:36px;line-height:44px">
    <span>VELTRAFIT</span><span class="brand-dot" style="width:26px;height:26px"></span>
  </div>
  <nav class="main-nav">
    <a class="active" style="left:578px" href="#">Home</a>
    <a style="left:677px" href="#">About Us</a>
    <a style="left:790px" href="#">Services</a>
    <a style="left:900px" href="#">Blog</a>
  </nav>
  <div class="btn" style="left:955px;top:18px;width:146px;height:51px">Contact Us</div>
</header>

<section class="hero">
  <div class="abs" role="img" aria-label="Smiling woman writing a meal plan beside fresh vegetables and fruit" style="inset:0"></div>
  <h1 class="hero-title">WELCOME TO<br>VELTRAFIT</h1>
  <p class="hero-text">Lorem ipsum dolor sit amet, consectetur adipiscing elit. Etiam ex mi, porta eu diam id, neque.</p>
  <div class="btn" style="left:97px;top:336px;width:146px;height:51px">Get Started</div>
  <span class="dot" style="left:32px;top:253px;background:#fff"></span>
  <span class="dot" style="left:32px;top:279px"></span>
  <span class="dot" style="left:32px;top:305px"></span>
</section>
<svg class="abs" style="left:0;top:660px" width="1200" height="100" viewBox="0 0 1200 100">
  <path d="M0 90 Q600 -40 1200 90 L1200 100 L0 100 Z" fill="#fff"/>
  <path d="M0 90 Q600 -40 1200 90 L1200 100 Q600 -20 0 100 Z" fill="#7f8a1b"/>
</svg>

<h2 class="section-title" style="left:102px;top:808px">About Us</h2>
<p class="about-text">Lorem ipsum dolor sit amet, consectetur adipiscing elit. Etiam ex mi, porta eu diam id, viverra tincidunt neque. Sed nisi urna, dignissim a suscipit non, dapibus ut ipsum. Aliquam erat volutpat. Aliquam rhoncus sodales elit quis fermentum. Curabitur posuere, ante vitae fermentum ornare, augue elit ullamcorper erat, vitae pretium ipsum mi eu nisi. Cras interdum rutrum pellentesque. Quisque ipsum tellus, molestie vel mi ut, condimentum pulvinar quam. Nunc non neque venenatis, consequat massa vitae, porta dui. Mauris consectetur tristique dictum.</p>
<div class="btn" style="left:97px;top:1127px;width:146px;height:51px">Read More</div>
<div class="abs" role="img" aria-label="Astronaut mascot illustration holding a flag within overlapping circles" style="left:628px;top:770px;width:440px;height:395px;border-radius:50%;background:radial-gradient(circle at 45% 50%,#8e9a1c 0%,#7f8a1b 45%,#5a1008 70%,#222 100%)"></div>

<svg class="abs" style="left:0;top:1225px" width="1200" height="735" viewBox="0 0 1200 735">
  <path d="M0 85 Q600 -10 1200 85 L1200 635 Q600 760 0 615 Z" fill="#7f8a1b"/>
  <path d="M0 85 Q600 -45 1200 85 Q600 -15 0 85 Z" fill="#7f8a1b"/>
  <path d="M0 655 Q600 780 1200 655 Q600 800 0 655 Z" fill="#7f8a1b"/>
</svg>
<h2 class="section-title" style="left:0;width:1200px;text-align:center;top:1333px;color:#fff">Our Services</h2>
<div class="service-photo" role="img" aria-label="Woman eating a fresh salad in a gym" style="left:99px;top:1411px;background:linear-gradient(160deg,#6d7a5a,#a89a4a 60%,#3d4a2a)"></div>
<div class="service-photo" role="img" aria-label="Trainer guiding a client through a seated stretch" style="left:439px;top:1411px;background:linear-gradient(160deg,#e8e4dc,#b09a7a 60%,#2a2a2a)"></div>
<div class="service-photo" role="img" aria-label="Man filming a workout on a phone tripod at home" style="left:782px;top:1411px;background:linear-gradient(160deg,#9a9a9a,#5a5a5a 60%,#2a2a2a)"></div>
<div class="service-name" style="left:88px;top:1755px">Diet Coaching</div>
<div class="service-name" style="left:428px;top:1755px">In-Person Coaching</div>
<div class="service-name" style="left:771px;top:1755px">Remote Coaching</div>

<h2 class="section-title" style="left:0;width:1200px;text-align:center;top:2020px">Contact Us</h2>
<div class="field" style="left:164px;top:2096px;width:423px;height:46px;padding-top:12px">Enter Name</div>
<div class="field" style="left:608px;top:2096px;width:423px;height:46px;padding-top:12px">Enter Email</div>
<div class="field" style="left:164px;top:2167px;width:873px;height:78px;padding:12px 26px">Message</div>
<div class="btn" style="left:527px;top:2277px;width:146px;height:51px">Submit</div>

<footer class="site-footer">
  <div class="brand" style="left:0;width:1200px;justify-content:center;top:110px;font-size:96px;line-height:110px;gap:22px">
    <span>VELTRAFIT</span><span class="brand-dot" style="width:60px;height:60px"></span>
  </div>
  <nav class="footer-nav">
    <a style="left:149px" href="#">Home</a>
    <a style="left:248px" href="#">About Us</a>
    <a style="left:369px" href="#">Services</a>
    <a style="left:487px" href="#">Blog</a>
    <a style="left:573px" href="#">Contact Us</a>
    <a style="left:713px" href="#">Privacy Policy</a>
    <a style="left:873px" href="#">Terms and Conditions</a>
  </nav>
  <div class="contact-icon" style="left:172px;top:334px">
    <svg width="26" height="20" viewBox="0 0 26 20"><rect x="1" y="1" width="24" height="18" fill="#fff"/><path d="M1 2 L13 11 L25 2" stroke="#1e1e1e" stroke-width="2" fill="none"/></svg>
  </div>
  <div class="contact-text" style="left:248px;top:338px">info@veltrafit.com</div>
  <div class="contact-icon" style="left:524px;top:334px">
    <svg width="24" height="24" viewBox="0 0 24 24"><circle cx="12" cy="12" r="10" fill="none" stroke="#fff" stroke-width="2"/><ellipse cx="12" cy="12" rx="4" ry="10" fill="none" stroke="#fff" stroke-width="2"/><line x1="2" y1="12" x2="22" y2="12" stroke="#fff" stroke-width="2"/></svg>
  </div>
  <div class="contact-text" style="left:593px;top:338px;color:#333">www.veltrafit.com</div>
  <div class="contact-icon" style="left:881px;top:334px">
    <svg width="22" height="22" viewBox="0 0 24 24"><path d="M6.6 10.8a15 15 0 0 0 6.6 6.6l2.2-2.2a1 1 0 0 1 1-.25 11.4 11.4 0 0 0 3.6.57 1 1 0 0 1 1 1V20a1 1 0 0 1-1 1A17 17 0 0 1 3 4a1 1 0 0 1 1-1h3.5a1 1 0 0 1 1 1c0 1.25.2 2.45.57 3.57a1 1 0 0 1-.25 1z" fill="#fff"/></svg>
  </div>
  <div class="contact-text" style="left:951px;top:338px">+1 555 014 2870</div>
  <div class="contact-text" style="left:0;width:1130px;text-align:center;top:440px;font-size:16px;color:#333">Copyrights@2023.VELTRAFIT.All Rights Reserved</div>
</footer>

</body>
</html>
```